My project benefits Military, First Responders, Police, Fire, and Educators.

Contact Information for Business Card

2 Sided appointment card. Visual side will have my head shot with "Brisk Lantern" in a bold graffic/text. I am picturing maybe the headshot applied to a filter that has a matrix effect where the picture is made up of data/numbers flowing vertically through the photo. I am of course open to other concepts as well. Side two will have contact info presented in an attractive visual complimenting the front.

```html
<!DOCTYPE html>
<html lang="en">
<head>
<meta charset="utf-8">
<title>Brisk Lantern — Appointment Card</title>
<link rel="stylesheet" href="https://fonts.googleapis.com/css2?family=Archivo+Black&family=Arimo:wght@400;700&family=Tinos&display=swap">
<style>
  :root {
    --page-bg: #e9e7e3;
    --card-white: #f6f6f5;
    --brand-green: #0f5a2e;
    --matrix-deep: #04200f;
    --matrix-mid: #0d5a2c;
    --matrix-glow: #2fa364;
    --title-grey: #d2d4d2;
    --name-grey: #6a6a6a;
    --text-grey: #555555;
  }
  * { margin: 0; padding: 0; box-sizing: border-box; }
  html, body { width: 1200px; height: 1000px; overflow: hidden; }
  body { background: var(--page-bg); position: relative; font-family: "Arimo", Arial, sans-serif; }

  .card {
    position: absolute;
    left: 210px;
    width: 780px;
    height: 446px;
    overflow: hidden;
    box-shadow: 0 10px 28px rgba(0,0,0,0.22);
  }

  /* Front */
  .card--front { top: 50px; background: var(--matrix-deep); }
  .front__portrait {
    position: absolute; inset: 0;
    background:
      radial-gradient(ellipse 30% 45% at 38% 45%, rgba(120,200,150,0.55), transparent 70%),
      linear-gradient(90deg, var(--matrix-deep) 0%, var(--matrix-mid) 35%, var(--matrix-glow) 55%, var(--matrix-mid) 75%, var(--matrix-deep) 100%);
  }
  .front__title {
    position: absolute;
    left: 470px; top: 110px;
    font-family: "Archivo Black", "Arial Black", sans-serif;
    font-size: 58px;
    line-height: 1.05;
    color: var(--title-grey);
  }

  /* Back */
  .card--back { top: 510px; background: var(--card-white); }
  .back__band { position: absolute; left: 0; top: 0; bottom: 0; width: 16px; background: var(--brand-green); }
  .back__name {
    position: absolute; left: 70px; top: 100px;
    font-weight: 700; font-size: 40px; color: var(--name-grey);
  }
  .back__role {
    position: absolute; left: 72px; top: 148px;
    font-size: 20px; letter-spacing: 0.35em; color: #808080;
  }
  .contact { position: absolute; left: 70px; display: flex; align-items: center; gap: 22px; color: var(--text-grey); }
  .contact--phone { top: 290px; font-family: "Tinos", "Times New Roman", serif; font-size: 21px; letter-spacing: 0.04em; }
  .contact--mail { top: 332px; font-size: 18px; }
  .contact svg { width: 20px; height: 20px; flex: none; }
  .address { position: absolute; left: 530px; top: 330px; color: var(--text-grey); font-size: 18px; line-height: 1.25; }
  .address__label { color: var(--brand-green); font-weight: 700; }
</style>
</head>
<body>
  <section class="card card--front">
    <div class="front__portrait" role="img" aria-label="Head-and-shoulders portrait of the client rendered as green digital rain of falling code"></div>
    <h1 class="front__title">“Brisk<br>Lantern”</h1>
  </section>

  <section class="card card--back">
    <div class="back__band"></div>
    <h2 class="back__name">NadimVoss</h2>
    <p class="back__role">Designer</p>

    <p class="contact contact--phone">
      <svg viewBox="0 0 24 24" aria-hidden="true"><path fill="#1f6b3c" d="M6.6 10.8a15 15 0 0 0 6.6 6.6l2.2-2.2a1 1 0 0 1 1-.25 11.4 11.4 0 0 0 3.6.57 1 1 0 0 1 1 1V20a1 1 0 0 1-1 1A17 17 0 0 1 3 4a1 1 0 0 1 1-1h3.5a1 1 0 0 1 1 1c0 1.25.2 2.45.57 3.6a1 1 0 0 1-.25 1z"/></svg>
      0170-482-653
    </p>
    <p class="contact contact--mail">
      <svg viewBox="0 0 24 24" aria-hidden="true"><rect x="2.5" y="5.5" width="19" height="13" fill="none" stroke="#5f9a74" stroke-width="1.6"/><path d="M2.5 5.5l9.5 7 9.5-7" fill="none" stroke="#5f9a74" stroke-width="1.6"/></svg>
      hello@brisklantern.com
    </p>

    <address class="address" style="font-style:normal">
      <span class="address__label">Address</span><br>
      48 Halden Row,<br>
      Marlow
    </address>
  </section>
</body>
</html>
```